Business Card Design Project

We are rebranding an existing automotive collision repair business. The business is called dent haven. I have attached logo but I'm not tied to that. I want to leave this wide open.

I want this card to say we are professional, competent, cutting edge. We are focused on customers and use a lot of the latest technology to make the customer experience different. We sign customers in on iPads. Paperwork I signed electronically and updates are sent via text, email, logging on a website or as they wish. I want this innovation and image to come through in our cards

Target Market(s)

60%. Women 40% men. Age 35-60

Industry/Entity Type

Automotive

Requirements
Must have
• The card must have name, title, phone,email, cell, web page

```html
<!DOCTYPE html>
<html lang="en">
<head>
<meta charset="utf-8">
<title>Dent Haven — Business Card</title>
<link rel="stylesheet" href="https://fonts.googleapis.com/css2?family=Montserrat:wght@300;400;600;800&display=swap">
<style>
  :root {
    --page-bg: #dedad8;
    --card-white: #f7f7f7;
    --card-grey-light: #e4e4e4;
    --slate: #5a5a5a;
    --slate-dark: #3e3e3e;
    --teal: #3aa9a8;
    --orange: #f29a3a;
    --green: #7dc242;
    --rule: #6d6d6d;
    --back-light: #7a7773;
    --back-dark: #3f3d3b;
    --white: #ffffff;
  }
  * { margin: 0; padding: 0; box-sizing: border-box; }
  html, body {
    width: 921px; height: 1200px; overflow: hidden;
    background: var(--page-bg);
    font-family: "Montserrat", sans-serif;
  }
  .card {
    position: absolute; left: 51px; width: 820px; height: 474px;
    box-shadow: 0 6px 14px rgba(0,0,0,0.25);
    overflow: hidden;
  }
  .card--front { top: 77px; background: linear-gradient(180deg, var(--card-white), var(--card-grey-light)); }
  .card--back {
    top: 617px; height: 476px;
    background: linear-gradient(90deg, var(--back-light), var(--back-dark));
    text-align: center; color: var(--white);
  }
  .card svg { display: block; }
  .brand-name { font-weight: 800; fill: var(--green); }
  .holder-name { fill: var(--orange); font-weight: 300; }
  .holder-name .strong { font-weight: 600; }
  .holder-title { fill: var(--slate-dark); font-weight: 300; }
  .contact-label-box { fill: var(--slate); }
  .contact-label { fill: var(--white); font-weight: 600; }
  .contact-value { fill: var(--orange); font-weight: 400; }
  .connector { fill: none; stroke: var(--rule); stroke-width: 1.3; }
  .node { fill: var(--orange); }

  .back-brand {
    position: absolute; top: 196px; left: 0; right: 0;
    font-size: 60px; font-weight: 800; color: var(--green); line-height: 1;
  }
  .back-web {
    position: absolute; top: 292px; left: 0; right: 0;
    font-size: 18px; font-weight: 600; letter-spacing: 1.5px;
  }
</style>
</head>
<body>
  <section class="card card--front" aria-label="Card front">
    <svg width="820" height="474" viewBox="0 0 820 474" font-family="Montserrat, sans-serif">
      <defs>
        <linearGradient id="slateFade" x1="0" y1="0" x2="1" y2="1">
          <stop offset="0" stop-color="#4a4a4a"/><stop offset="1" stop-color="#7a7a7a"/>
        </linearGradient>
        <linearGradient id="tealFade" x1="0" y1="0" x2="1" y2="1">
          <stop offset="0" stop-color="#7cb6be"/><stop offset="1" stop-color="#5a9ea8"/>
        </linearGradient>
      </defs>
      <polygon points="378,0 686,0 469,143" fill="url(#slateFade)"/>
      <polygon points="820,183 820,474 653,474 583,343" fill="url(#tealFade)"/>
      <polygon points="0,436 309,236 309,250 0,450" fill="var(--teal)"/>

      <g class="connectors">
        <polyline class="connector" points="407,245 225,368 225,474"/>
        <polyline class="connector" points="440,276 269,388 269,474"/>
        <polyline class="connector" points="338,388 299,415 299,474"/>
        <polyline class="connector" points="476,351 344,435 344,474"/>
        <circle class="node" cx="407" cy="245" r="15"/>
        <circle class="node" cx="440" cy="276" r="15"/>
        <circle class="node" cx="338" cy="388" r="15"/>
        <circle class="node" cx="476" cy="351" r="15"/>
      </g>

      <text class="brand-name" font-size="40" transform="translate(86,246) rotate(-33)">Dent Haven</text>

      <text class="holder-name" font-size="30" transform="translate(107,346) rotate(-33)">YOUR <tspan class="strong">NAME HERE</tspan></text>
      <text class="holder-title" font-size="24" transform="translate(318,242) rotate(-33)">TITLE</text>

      <g transform="translate(439,222) rotate(-33)">
        <rect class="contact-label-box" x="-4" y="-18" width="44" height="24"/>
        <text class="contact-label" font-size="18">PH:</text>
        <text class="contact-value" font-size="19" x="46">000 0000 000</text>
      </g>
      <g transform="translate(469,256) rotate(-33)">
        <rect class="contact-label-box" x="-4" y="-18" width="60" height="24"/>
        <text class="contact-label" font-size="18">CELL:</text>
        <text class="contact-value" font-size="19" x="62">000 0000 000</text>
      </g>
      <g transform="translate(373,370) rotate(-33)">
        <rect class="contact-label-box" x="-4" y="-18" width="76" height="24"/>
        <text class="contact-label" font-size="18">EMAIL:</text>
        <text class="contact-value" font-size="19" x="78">INFO@DENTHAVEN.COM</text>
      </g>
      <g transform="translate(503,329) rotate(-33)">
        <rect class="contact-label-box" x="-4" y="-18" width="60" height="24"/>
        <text class="contact-label" font-size="18">WEB:</text>
        <text class="contact-value" font-size="19" x="62">DENTHAVEN.COM</text>
      </g>
    </svg>
  </section>

  <section class="card card--back" aria-label="Card back">
    <p class="back-brand">Dent Haven</p>
    <p class="back-web">DENTHAVEN.COM</p>
  </section>
</body>
</html>
```